Brochure for a website accessibility report

This brochure is related to a report that www.qelvantrix.org sell. The report shows the results of an automated audit of a websites accessibility. It shows details of issues found with screen shots, examples of code and provides remediation advice.

The brochure will be a pdf 8.5 inches by 11 inches. It can be anywhere from 6 to 10 pages.

The FlintVue™ name itself should be “Bree Serif” font. The fonts, styles, colors and sizes are up to you.

The images used and logo of the Office of Digital Reachworks and K7P logo are upload

We highlighted in blue page extracts from the report we sell. Do not use the blue highlight, it is merely there to show you where the specific examples of the report we sell are vs the other content in the report. The areas in blue which show the content from the actual report should be shown as an extract of the actual page of the report. You have flexibility to change the layout and the way the content look.

The red square callouts over the blue content are callouts that describe the specific page extracts. We used it as a red callout only so that you would be able to see it. You should change the specific location, look and feel of the callout to be appropriate

Target Market(s)

Marketing and Technical people

Industry/Entity Type

Information Technology

Font styles to use
Sans Serif

Colors

Designer to choose colors to be used in the design.

Requirements
Should not have
• wheelchairs, images of blind people

```html
<!DOCTYPE html>
<html lang="en">
<head>
<meta charset="utf-8">
<title>Section 1 – Summary Chart</title>
<link href="https://fonts.googleapis.com/css2?family=Bree+Serif&family=Roboto:wght@300;400;500&display=swap" rel="stylesheet">
<style>
  :root {
    --navy: #0b3a5c;
    --blue-mid: #2f86c0;
    --blue-light: #3a9fd6;
    --heading-blue: #2e86c1;
    --text-grey: #555a5f;
    --ink: #111;
    --gold: #f5c842;
    --white: #ffffff;
  }
  * { box-sizing: border-box; margin: 0; padding: 0; }
  html, body { width: 927px; height: 1200px; overflow: hidden; background: var(--white); }
  body { position: relative; font-family: "Roboto", sans-serif; color: var(--text-grey); }

  .section-title {
    position: absolute; left: 52px; top: 76px;
    font-family: "Bree Serif", serif; font-size: 32px; color: var(--heading-blue); letter-spacing: .3px;
  }
  .lead { position: absolute; left: 52px; width: 824px; font-size: 16px; font-weight: 300; line-height: 20px; }
  .lead--intro { top: 130px; }
  .lead--note { top: 209px; }
  .lead--after { top: 744px; text-align: justify; }
  .chart-label { position: absolute; left: 52px; top: 169px; font-size: 16px; font-weight: 500; color: var(--ink); }

  .summary-chart {
    position: absolute; left: 84px; top: 297px; width: 759px;
    border-radius: 22px; overflow: hidden;
    box-shadow: 0 6px 16px rgba(0,0,0,.25);
  }
  .summary-chart table { width: 100%; border-collapse: collapse; color: var(--white); }
  .summary-chart th {
    background: var(--navy); height: 51px;
    font-family: "Bree Serif", serif; font-weight: 400; font-size: 15px; letter-spacing: .4px;
    border-right: 1px solid rgba(0,0,0,.25);
  }
  .summary-chart th:first-child { text-align: left; padding-left: 24px; width: 195px; }
  .summary-chart th:nth-child(2) { width: 281px; }
  .summary-chart td { height: 31.8px; font-size: 16px; font-weight: 300; vertical-align: middle; }
  .principle {
    font-family: "Bree Serif", serif; font-size: 14px !important; font-weight: 400 !important;
    letter-spacing: .4px; padding-left: 31px;
  }
  .principle--mid { background: var(--blue-mid); }
  .principle--light { background: var(--blue-light); }
  .row--mid .guideline, .row--mid .issues { background: var(--blue-mid); }
  .row--light .guideline, .row--light .issues { background: var(--blue-light); }
  .guideline { padding-left: 31px; border-bottom: 1px solid rgba(0,0,0,.06); }
  .guideline .num { display: inline-block; width: 47px; }
  .issues { padding-left: 25px; font-size: 14.5px !important; }
  .issues span { display: inline-block; width: 51px; }

  .example-label { position: absolute; left: 101px; top: 806px; font-size: 17px; color: var(--heading-blue); letter-spacing: .3px; }

  .principle-panel {
    position: absolute; left: 52px; top: 840px; width: 822px; height: 380px;
    background: var(--navy); border-radius: 44px 44px 0 0; color: var(--white);
    box-shadow: 0 -2px 12px rgba(0,0,0,.08);
  }
  .principle-panel .kicker { position: absolute; left: 51px; top: 49px; font-size: 14px; font-weight: 500; }
  .principle-panel h2 {
    position: absolute; left: 51px; top: 65px;
    font-family: "Bree Serif", serif; font-weight: 400; font-size: 32px; color: var(--gold);
  }
  .principle-panel p { position: absolute; left: 51px; width: 722px; font-size: 16px; font-weight: 300; line-height: 20px; }
  .principle-panel .principle-desc { top: 120px; }
  .principle-panel h3 { position: absolute; left: 51px; top: 244px; font-size: 16px; font-weight: 500; }
  .principle-panel .guideline-desc { top: 270px; }
</style>
</head>
<body>
  <h1 class="section-title">SECTION 1</h1>
  <p class="lead lead--intro">The first section of the report begins with a Summary Chart that breaks down WCAG 2.1 A/AA issues by principle:</p>
  <p class="chart-label">Example WCAG 2.1 A/AA Summary Chart</p>
  <p class="lead lead--note">Checkpoints with failures detected are identified in the "Issues Discovered" column. The detail behind these failures is available in the next section.</p>

  <div class="summary-chart">
    <table>
      <thead>
        <tr><th>UNDERSTANDABLE</th><th>GUIDELINE</th><th>ISSUES DISCOVERED</th></tr>
      </thead>
      <tbody>
        <tr class="row--mid"><td class="principle principle--mid" rowspan="4">PERCEIVABLE</td><td class="guideline"><span class="num">1.1</span>Text Alternatives</td><td class="issues"><span>1.1</span></td></tr>
        <tr class="row--light"><td class="guideline"><span class="num">1.2</span>Time-based Media</td><td class="issues"><span>1.2.1</span> <span>1.2.2</span> <span>1.2.3</span> <span>1.2.4</span> <span>1.2.5</span></td></tr>
        <tr class="row--mid"><td class="guideline"><span class="num">1.3</span>Adaptable</td><td class="issues"><span>1.3.1</span> <span>1.3.2</span> <span>1.3.5</span></td></tr>
        <tr class="row--light"><td class="guideline"><span class="num">1.4</span>Distinguishable</td><td class="issues"><span>1.4.1</span> <span>1.4.3</span> <span>1.4.4</span> <span>1.4.11</span></td></tr>
        <tr class="row--mid"><td class="principle principle--light" rowspan="3">OPERABLE</td><td class="guideline"><span class="num">2.1</span>Keyboard Accessible</td><td class="issues"><span>2.1.1</span> <span>2.1.2</span></td></tr>
        <tr class="row--light"><td class="guideline"><span class="num">2.2</span>Enough Time</td><td class="issues"><span>2.2.1</span> <span>2.2.2</span></td></tr>
        <tr class="row--mid"><td class="guideline"><span class="num">2.4</span>Navigable</td><td class="issues"><span>2.4.1</span> <span>2.4.2</span> <span>2.4.4</span> <span>2.4.7</span></td></tr>
        <tr class="row--light"><td class="principle principle--mid" rowspan="3">UNDERSTANDABLE</td><td class="guideline"><span class="num">3.1</span>Readable</td><td class="issues"><span>3.1.1</span></td></tr>
        <tr class="row--mid"><td class="guideline"><span class="num">3.2</span>Predictable</td><td class="issues"><span>3.2.1</span> <span>3.2.2</span></td></tr>
        <tr class="row--light"><td class="guideline"><span class="num">3.3</span>Input Assistance</td><td class="issues"><span>3.3.2</span></td></tr>
        <tr class="row--mid"><td class="principle principle--light">ROBUST</td><td class="guideline"><span class="num">4.1</span>Compatible</td><td class="issues"><span>4.1.1</span> <span>4.1.2</span></td></tr>
      </tbody>
    </table>
  </div>

  <p class="lead lead--after">The report then provides full detail about the specific infractions organized by each of the four principles and explains exactly what the problems are.</p>

  <p class="example-label">EXAMPLE:</p>

  <section class="principle-panel">
    <p class="kicker">PRINCIPLE 1</p>
    <h2>Perceivable</h2>
    <p class="principle-desc">Information and user interface components must be presentable to users in ways they can perceive. This means that users must be able to perceive the information being presented (it can't be invisible to all of their senses). Provide text alternatives for nontext content. Provide captions and other alternatives for multimedia. Create content that can be presented in different ways, including by assistive technologies, without losing meaning. Make it easier for users to see and hear content.</p>
    <h3>GUIDELINE 1.1 TEXT ALTERNATIVES</h3>
    <p class="guideline-desc">Provide text alternatives for any non-text content so that it can be changed into other forms people need, such as large print, braille, speech, symbols or simpler language.</p>
  </section>
</body>
</html>
```